Post card for Tax Preparation Services

Bramble Ledger, a accounting and tax solution firm is in need of a postcard to send to people who have moved into the area in the last year. The goal is to market our tax preparation services. More information on our business and services can be found on our website: www.brambleledger-example.com

Return address:
4815 Quarry Mill Blvd
Bldg 400, Ste 310
Woodstock, GA 30189

Phone: (555) 555-4LDG

Please submit copies of front and back design in one submisstion. Do not submit duplicate designs.

Target Market(s)

People who have moved within 2 miles of our office

Industry/Entity Type

Accounting

Colors
6b449b
fbee3e

Requirements
Must have
• Logo
• Schedule Online
• Mention this postcard Receive $25.00 off tax prep
• Colors Gold #c6A734 and Purple #5f1547 to match logo
Should not have
• No cartoony feel

```html
<!DOCTYPE html>
<html lang="en">
<head>
<meta charset="utf-8">
<title>Bramble Ledger Postcard</title>
<link rel="stylesheet" href="https://fonts.googleapis.com/css2?family=Open+Sans:wght@300;400;600;700;800&display=swap">
<style>
  :root {
    --gold: #c6a734;
    --purple: #7d0f7d;
    --ink: #1e1e1e;
    --silver: #c9c9c9;
    --backdrop: #6e6e6e;
    --white: #ffffff;
    --rule: #9a9a9a;
  }
  * { box-sizing: border-box; margin: 0; padding: 0; }
  html, body { width: 880px; height: 1200px; overflow: hidden; }
  body {
    background: var(--backdrop);
    font-family: "Open Sans", Arial, sans-serif;
    color: var(--ink);
    position: relative;
  }
  .card {
    position: absolute;
    left: 54px;
    width: 772px;
    height: 551px;
    background: var(--white);
    overflow: hidden;
  }
  .card--front { top: 39px; }
  .card--back { top: 615px; }
  .layer { position: absolute; left: 0; top: 0; }

  .brand { position: absolute; display: flex; align-items: center; white-space: nowrap; }
  .brand__mark { border-radius: 50%; background: var(--gold); flex: none; }
  .brand__text { display: flex; flex-direction: column; line-height: 1; }
  .brand__name { color: var(--gold); font-weight: 700; }
  .brand__tag { color: var(--ink); font-weight: 400; letter-spacing: .8px; margin-top: 3px; }

  .front-brand { left: 42px; top: 40px; gap: 14px; }
  .front-brand .brand__mark { width: 62px; height: 62px; }
  .front-brand .brand__name { font-size: 29px; }
  .front-brand .brand__tag { font-size: 11.5px; }

  .headline { position: absolute; left: 42px; top: 116px; color: var(--purple); font-weight: 800; line-height: 60px; white-space: nowrap; }
  .headline__lead { font-weight: 300; color: var(--ink); font-size: 40px; }
  .headline__big { font-size: 64px; }
  .intro { position: absolute; left: 42px; top: 248px; width: 340px; font-size: 17.5px; line-height: 1.37; }
  .offer { position: absolute; left: 42px; top: 306px; width: 360px; font-size: 17px; font-weight: 800; line-height: 1.4; color: var(--purple); }
  .offer__lead { color: var(--gold); }

  .band-gold { position: absolute; left: 0; right: 0; top: 413px; height: 85px; background: var(--gold); }
  .band-purple { position: absolute; left: 0; right: 0; top: 498px; height: 53px; background: var(--purple); white-space: nowrap;
    color: var(--white); font-size: 23px; letter-spacing: .5px; display: flex; align-items: center; justify-content: center; gap: 8px; }
  .band-purple strong { font-weight: 800; }

  .phone-pill { position: absolute; left: 60px; top: 375px; width: 362px; height: 58px; border-radius: 0 29px 29px 0; white-space: nowrap;
    background: var(--purple); color: var(--white); font-size: 36px; font-weight: 800; display: flex; align-items: center; padding-left: 54px; }
  .phone-badge { position: absolute; left: 35px; top: 369px; width: 70px; height: 70px; border-radius: 50%; background: #2a1f22; }
  .schedule { position: absolute; left: 0; right: 0; top: 450px; height: 34px; color: var(--white); font-size: 24px; font-weight: 800;
    display: flex; justify-content: center; align-items: center; gap: 10px; white-space: nowrap; }

  /* back */
  .services-title { position: absolute; left: 41px; top: 40px; font-size: 26px; font-weight: 400; white-space: nowrap; }
  .services-title span { color: var(--gold); font-weight: 700; }
  .services { position: absolute; left: 41px; top: 83px; list-style: none; }
  .services li { font-size: 15.5px; font-weight: 700; height: 27.5px; display: flex; align-items: center; gap: 5px; white-space: nowrap; }
  .quote-open { position: absolute; left: 41px; top: 206px; font-size: 52px; font-weight: 800; line-height: 1; height: 26px; overflow: hidden; }
  .testimonial { position: absolute; left: 41px; top: 235px; width: 258px; font-size: 13.5px; line-height: 18.7px; }
  .attribution { position: absolute; left: 120px; top: 297px; font-size: 13.5px; font-weight: 700; color: var(--purple); white-space: nowrap; }
  .quote-close { position: absolute; left: 270px; top: 295px; font-size: 52px; font-weight: 800; line-height: 1; height: 26px; overflow: hidden; }

  .contact-band { position: absolute; left: 0; top: 339px; width: 380px; height: 107px; background: var(--purple); color: var(--white); }
  .contact-row { position: absolute; left: 50px; white-space: nowrap; line-height: 1; }
  .contact-row svg { position: absolute; left: -30px; top: 50%; transform: translateY(-50%); }
  .contact-email { top: 14px; font-size: 15px; }
  .contact-phone { top: 38px; font-size: 27px; font-weight: 800; }
  .contact-web { top: 76px; font-size: 15.5px; }

  .back-brand { left: 414px; top: 60px; gap: 8px; }
  .back-brand .brand__mark { width: 30px; height: 30px; }
  .back-brand .brand__name { font-size: 17.5px; }
  .back-brand .brand__tag { font-size: 7.6px; letter-spacing: .5px; }
  .stamp-box { position: absolute; left: 630px; top: 40px; width: 98px; height: 95px; border: 1px solid var(--rule); }
  .return-address { position: absolute; right: 44px; top: 182px; text-align: right; font-size: 12.5px; line-height: 1.36; font-style: normal; }
  .address-line { position: absolute; left: 480px; width: 248px; height: 1px; background: var(--rule); }
</style>
</head>
<body>

<section class="card card--front">
  <svg class="layer" width="772" height="551" viewBox="0 0 772 551" aria-hidden="true">
    <path d="M405 0 L458 0 C430 120 432 300 478 413 L440 413 C385 300 385 120 405 0 Z" fill="var(--gold)"/>
    <path d="M458 0 L472 0 C444 120 448 300 492 413 L478 413 C432 300 430 120 458 0 Z" fill="var(--silver)"/>
  </svg>
  <svg class="layer" width="772" height="551" viewBox="0 0 772 551" role="img" aria-label="Portrait photo of the firm's accountant in front of a brick wall">
    <defs>
      <linearGradient id="portraitTone" x1="0" y1="0" x2="1" y2="1">
        <stop offset="0" stop-color="#a45a3e"/>
        <stop offset="1" stop-color="#6a3a2c"/>
      </linearGradient>
    </defs>
    <path d="M472 0 L772 0 L772 413 L492 413 C448 300 444 120 472 0 Z" fill="url(#portraitTone)"/>
  </svg>

  <div class="brand front-brand">
    <span class="brand__mark"></span>
    <span class="brand__text">
      <span class="brand__name">BRAMBLE LEDGER</span>
      <span class="brand__tag">ACCOUNTING &amp; TAX SOLUTIONS</span>
    </span>
  </div>

  <h1 class="headline"><span class="headline__lead">WE'RE </span><span class="headline__big">YOUR</span><br><span class="headline__big">PARTNER</span></h1>
  <p class="intro">Get your mind off of the numbers and back on business.</p>
  <p class="offer"><span class="offer__lead">Call today for a</span> FREE NO-OBLIGATION CONSULTATION.</p>

  <div class="band-gold"></div>
  <div class="phone-pill">(555) 555-4LDG</div>
  <div class="phone-badge">
    <svg width="70" height="70" viewBox="0 0 70 70" aria-hidden="true">
      <circle cx="35" cy="35" r="24" fill="none" stroke="#fff" stroke-width="3"/>
      <path d="M27 23 l5 -2 l4 8 l-4 3 c2 5 5 8 9 10 l3 -4 l8 4 l-2 5 c-12 1 -24 -12 -23 -24 Z" fill="#fff"/>
    </svg>
  </div>
  <p class="schedule"><span>Schedule Online</span>
    <svg width="20" height="20" viewBox="0 0 22 22" aria-hidden="true"><g fill="none" stroke="#fff" stroke-width="1.6"><circle cx="11" cy="11" r="9"/><ellipse cx="11" cy="11" rx="4" ry="9"/><path d="M2 11h18M4 6h14M4 16h14"/></g></svg>
    <span>www.BrambleLedger-example.com</span></p>
  <p class="band-purple">MENTION THIS POSTCARD RECEIVE <strong>$25.00 OFF TAX PREP</strong></p>
</section>

<section class="card card--back">
  <svg class="layer" width="772" height="551" viewBox="0 0 772 551" role="img" aria-label="Faded background photo of a desk with laptop and financial papers">
    <path d="M0 0 L378 0 C318 100 302 240 342 339 L0 339 Z" fill="#eceef0"/>
  </svg>
  <svg class="layer" width="772" height="551" viewBox="0 0 772 551" role="img" aria-label="Street map showing the office location">
    <path d="M0 446 L392 446 C402 490 385 525 350 551 L0 551 Z" fill="#eef0f2"/>
  </svg>
  <svg class="layer" width="772" height="551" viewBox="0 0 772 551" aria-hidden="true">
    <path d="M380 0 L438 0 C362 100 352 240 410 339 C468 430 452 500 388 551 L356 551 C418 500 428 430 370 339 C312 240 320 100 380 0 Z" fill="var(--gold)"/>
    <path d="M382 0 C320 100 304 240 346 339" fill="none" stroke="var(--purple)" stroke-width="6"/>
    <path d="M396 446 C408 495 390 530 352 551" fill="none" stroke="var(--purple)" stroke-width="6"/>
  </svg>

  <h2 class="services-title">OUR <span>SERVICES</span></h2>
  <ul class="services">
    <li><svg width="14" height="12" viewBox="0 0 14 12" aria-hidden="true"><path d="M1 6 l4 4 l8 -9" fill="none" stroke="var(--gold)" stroke-width="2"/></svg>TAX PREPARATION &amp; PLANNING</li>
    <li><svg width="14" height="12" viewBox="0 0 14 12" aria-hidden="true"><path d="M1 6 l4 4 l8 -9" fill="none" stroke="var(--gold)" stroke-width="2"/></svg>ACCOUNTING &amp; BOOKKEEPING</li>
    <li><svg width="14" height="12" viewBox="0 0 14 12" aria-hidden="true"><path d="M1 6 l4 4 l8 -9" fill="none" stroke="var(--gold)" stroke-width="2"/></svg>IRS TAX RESOLUTION</li>
    <li><svg width="14" height="12" viewBox="0 0 14 12" aria-hidden="true"><path d="M1 6 l4 4 l8 -9" fill="none" stroke="var(--gold)" stroke-width="2"/></svg>PAYROLL SERVICES</li>
  </ul>
  <span class="quote-open">“</span>
  <p class="testimonial">Dana is very helpful and sorted out our back taxes and saved us a lot of money. Highly recommend!</p>
  <p class="attribution">Lena M (Marietta, GA)</p>
  <span class="quote-close">”</span>

  <div class="contact-band">
    <p class="contact-row contact-email"><svg width="18" height="14" viewBox="0 0 18 14" aria-hidden="true"><g fill="none" stroke="#fff" stroke-width="1.4"><rect x="1" y="1" width="16" height="12"/><path d="M1 1 l8 7 l8 -7"/></g></svg>dana@brambleledger-example.com</p>
    <p class="contact-row contact-phone"><svg width="22" height="22" viewBox="0 0 22 22" aria-hidden="true"><circle cx="11" cy="11" r="9.5" fill="none" stroke="#fff" stroke-width="1.6"/><path d="M8 6 l2 -1 l2 4 l-2 1 c1 2 2 3 4 4 l1 -2 l4 2 l-1 2 c-5 1 -11 -5 -10 -10 Z" fill="#fff"/></svg>(555) 555-4LDG</p>
    <p class="contact-row contact-web"><svg width="20" height="20" viewBox="0 0 22 22" aria-hidden="true"><g fill="none" stroke="#fff" stroke-width="1.6"><circle cx="11" cy="11" r="9"/><ellipse cx="11" cy="11" rx="4" ry="9"/><path d="M2 11h18M4 6h14M4 16h14"/></g></svg>www.brambleledger-example.com</p>
  </div>

  <svg class="layer" width="772" height="551" viewBox="0 0 772 551" aria-hidden="true">
    <circle cx="375" cy="397" r="78" fill="var(--gold)"/>
  </svg>
  <svg class="layer" width="772" height="551" viewBox="0 0 772 551" role="img" aria-label="Round photo of a small business owner working on a laptop">
    <circle cx="375" cy="397" r="71" fill="#b9c4c8"/>
  </svg>

  <div class="brand back-brand">
    <span class="brand__mark"></span>
    <span class="brand__text">
      <span class="brand__name">BRAMBLE LEDGER</span>
      <span class="brand__tag">ACCOUNTING &amp; TAX SOLUTIONS</span>
    </span>
  </div>
  <div class="stamp-box"></div>
  <address class="return-address">Return address:<br>4815 Quarry Mill Blvd<br>Bldg 400, Ste 310<br>Woodstock, GA 30189</address>
  <div class="address-line" style="top:312px"></div>
  <div class="address-line" style="top:358px"></div>
  <div class="address-line" style="top:406px"></div>
</section>

</body>
</html>
```